Verodex business card

Business card for sustainable investment company called "Verodex". Verodex is an exchange platform selling carbon credits between buyers and sellers. Carbon Credits are an environmental commodity for reducing global carbon emissions.

the card should obviously have our logo and the theme should be sustainability/environment mixed with a trading platform.

Contact Information for Business Card

Logo, Name, Title, Phone, Email

Colors
0054AA
0677BA
7BADD7
CADEEF
E8F1F8
0094D4
00A9DD
6FCCEA
C7EBF8
E9F6FB
00AB8E
00BBA5
67D7C9
C6EFE9
E9F9F6
59FF00
82FF00
B8FF75
E3FFCB
F4FFEA

```html
<!DOCTYPE html>
<html lang="en">
<head>
<meta charset="UTF-8">
<title>Verodex Business Card</title>
<link href="https://fonts.googleapis.com/css2?family=Montserrat:wght@400;500;600&display=swap" rel="stylesheet">
<style>
  :root {
    --backdrop: #229db2;
    --paper: #e9e4d9;
    --paper-shade: #e2dccf;
    --ink-navy: #1c2b3e;
    --ink-body: #2f3238;
    --accent-teal: #00a9dd;
    --accent-blue: #0677ba;
    --divider: #6b665c;
  }
  * { margin: 0; padding: 0; box-sizing: border-box; }
  html, body {
    width: 1200px; height: 1200px; overflow: hidden;
    background: var(--backdrop);
    font-family: "Montserrat", sans-serif;
  }
  .stage {
    width: 1200px; height: 1200px;
    display: flex; flex-direction: column; align-items: center; justify-content: center;
    gap: 60px;
  }
  .card {
    width: 840px; height: 480px;
    border-radius: 34px;
    background: radial-gradient(ellipse at 30% 30%, var(--paper), var(--paper-shade));
    box-shadow: 0 10px 24px rgba(0, 40, 50, 0.28);
    position: relative;
  }
  /* front */
  .card-front .contact {
    position: absolute; left: 70px; top: 150px;
  }
  .identity {
    display: flex; gap: 12px; align-items: stretch; margin-bottom: 26px;
  }
  .identity-bar {
    width: 6px;
    background: linear-gradient(var(--accent-teal), var(--accent-blue));
  }
  .full-name {
    font-size: 38px; font-weight: 500; letter-spacing: -0.5px;
    color: var(--accent-teal); line-height: 1;
  }
  .position {
    font-size: 20px; color: var(--ink-body); letter-spacing: 0.5px; margin-top: 4px;
  }
  .details { list-style: none; }
  .details li {
    display: flex; align-items: center; gap: 14px;
    font-size: 24px; color: var(--ink-body); margin-bottom: 12px;
  }
  .details svg { width: 26px; height: 26px; flex: none; }
  .divider {
    position: absolute; left: 420px; top: 150px;
    width: 1px; height: 180px; background: var(--divider);
  }
  .brand {
    position: absolute;
    display: flex; align-items: center; gap: 18px;
    color: var(--ink-navy); font-weight: 600; letter-spacing: 1px;
  }
  .brand-square { background: var(--accent-blue); }
  .card-front .brand { left: 480px; top: 205px; font-size: 50px; }
  .card-front .brand-square { width: 36px; height: 36px; }
  .card-back .brand { left: 50%; top: 50%; transform: translate(-50%, -50%); font-size: 78px; gap: 26px; }
  .card-back .brand-square { width: 56px; height: 56px; }
</style>
</head>
<body>
<main class="stage">
  <section class="card card-front">
    <div class="contact">
      <div class="identity">
        <span class="identity-bar"></span>
        <div>
          <p class="full-name">FULL NAME</p>
          <p class="position">POSITION</p>
        </div>
      </div>
      <ul class="details">
        <li>
          <svg viewBox="0 0 24 24" aria-hidden="true"><path fill="#0677ba" d="M6.6 10.8a15 15 0 0 0 6.6 6.6l2.2-2.2c.3-.3.7-.4 1-.2 1.1.4 2.3.6 3.6.6.6 0 1 .4 1 1V20c0 .6-.4 1-1 1A17 17 0 0 1 3 4c0-.6.4-1 1-1h3.5c.6 0 1 .4 1 1 0 1.3.2 2.5.6 3.6.1.3 0 .7-.2 1z"/></svg>
          (000) 000 0000
        </li>
        <li>
          <svg viewBox="0 0 24 24" aria-hidden="true"><rect x="2" y="5" width="20" height="14" fill="#0677ba"/><path d="M2 5l10 8 10-8" fill="none" stroke="#e9e4d9" stroke-width="1.5"/></svg>
          email@company.com
        </li>
        <li>
          <svg viewBox="0 0 24 24" aria-hidden="true"><g fill="none" stroke="#0677ba" stroke-width="1.6"><circle cx="12" cy="12" r="9.5"/><ellipse cx="12" cy="12" rx="4.5" ry="9.5"/><path d="M2.5 12h19M4 7h16M4 17h16"/></g></svg>
          www.company.com
        </li>
      </ul>
    </div>
    <span class="divider"></span>
    <div class="brand"><span class="brand-square"></span>VERODEX</div>
  </section>

  <section class="card card-back">
    <div class="brand"><span class="brand-square"></span>VERODEX</div>
  </section>
</main>
</body>
</html>
```